Machining Business Order Thank You Insert

I am looking for a business style card to include with orders that I ship. The card needs to thank the recipient for their order, and encourage them to leave a review. The card should include my business name and contact information and have an area to hand write a message.

I mainly sale on Craftlane and my own website. We are a machining an manufacturing business that are in the sale of mostly metal machined and 3d printed plastic products.

The front of the card should include the following:
Logo: (attached)
Snapgram: https://www.snapgram.example/kelvomill/
Friendsbook: https://www.friendsbook.example/KelvoMill
Website: https://www.kelvomill.example/

The back of the card needs an area to write a message

Industry/Entity Type

3D Printing, Machining, Craftlane

Contact Information for Business Card

Black or white front, white back to write a personal message

Font styles to use
Sans Serif

Colors

Designer to choose colors to be used in the design.

Requirements
Must have
• Encourage a review, social media info

```html
<!DOCTYPE html>
<html lang="en">
<head>
<meta charset="utf-8">
<title>KelvoMill Order Thank You Insert</title>
<link rel="stylesheet" href="https://fonts.googleapis.com/css2?family=Saira+Semi+Condensed:wght@400;500&display=swap">
<style>
  :root {
    --backdrop: #2e2e30;
    --card-edge: #151516;
    --card-face: #1d1c1e;
    --accent-orange: #f15a24;
    --steel-grey: #6f6e70;
    --ink-white: #f2f2f2;
    --note-paper: #ffffff;
    --note-rule: #c9c9cb;
  }
  * { margin: 0; padding: 0; box-sizing: border-box; }
  html, body {
    width: 1125px;
    height: 1200px;
    overflow: hidden;
    background: var(--backdrop);
  }
  .canvas {
    position: relative;
    width: 1125px;
    height: 1200px;
    font-family: "Saira Semi Condensed", Arial, sans-serif;
  }
  .card-shapes {
    position: absolute;
    inset: 0;
  }
  .centered-line {
    position: absolute;
    left: 357px;
    width: 400px;
    text-align: center;
  }
  .thanks-heading {
    top: 234px;
    font-size: 20px;
    line-height: 24px;
    font-weight: 500;
    color: var(--accent-orange);
  }
  .contact-mark {
    top: 278px;
    font-size: 15px;
    line-height: 18px;
    font-weight: 500;
    letter-spacing: 4px;
    color: var(--steel-grey);
  }
  .contact-lines {
    top: 318px;
    font-size: 20px;
    line-height: 25px;
    font-weight: 400;
    color: var(--ink-white);
  }
  .social-row {
    top: 400px;
    display: flex;
    justify-content: center;
    gap: 16px;
    font-size: 14px;
    line-height: 18px;
    color: var(--accent-orange);
  }
  .social-item {
    display: flex;
    align-items: center;
    gap: 5px;
  }
  .social-dot {
    width: 12px;
    height: 12px;
    border-radius: 50%;
    background: var(--accent-orange);
  }
  .review-prompt {
    top: 434px;
    font-size: 15px;
    line-height: 19px;
    color: var(--ink-white);
  }
  .note-area {
    position: absolute;
    top: 738px;
    left: 427px;
    width: 260px;
    height: 112px;
    padding: 10px 16px;
    background: var(--note-paper);
    border-radius: 6px;
  }
  .note-label {
    font-size: 13px;
    line-height: 16px;
    font-weight: 500;
    color: var(--steel-grey);
    text-align: center;
  }
  .note-rule {
    height: 1px;
    margin-top: 22px;
    background: var(--note-rule);
  }
  .brand-name {
    top: 884px;
    font-size: 28px;
    line-height: 34px;
    font-weight: 500;
    letter-spacing: 9px;
    color: var(--accent-orange);
  }
</style>
</head>
<body>
<main class="canvas">
  <svg class="card-shapes" width="1125" height="1200" viewBox="0 0 1125 1200" aria-hidden="true">
    <polygon points="150,366 557,131 967,366 557,601" fill="var(--card-edge)"/>
    <polygon points="173,366 557,148 942,366 557,584" fill="var(--card-face)"/>
    <polyline points="557,148 173,366 557,584" fill="none" stroke="var(--accent-orange)" stroke-width="5"/>
    <polyline points="557,148 942,366 557,584" fill="none" stroke="var(--steel-grey)" stroke-width="5"/>

    <polygon points="150,878 557,642 967,878 557,1112" fill="var(--card-edge)"/>
    <polygon points="173,878 557,658 942,878 557,1096" fill="var(--card-face)"/>
    <polyline points="557,658 173,878 557,1096" fill="none" stroke="var(--steel-grey)" stroke-width="5"/>
    <polyline points="557,658 942,878 557,1096" fill="none" stroke="var(--accent-orange)" stroke-width="5"/>
  </svg>

  <section class="contact-card">
    <h1 class="centered-line thanks-heading">Thank you for your order!</h1>
    <div class="centered-line contact-mark">KELVOMILL</div>
    <div class="centered-line contact-lines">
      <p>Millbrook, IN</p>
      <p>kelvomillcnc@mailbox.example</p>
      <p>www.kelvomill.example</p>
    </div>
    <div class="centered-line social-row">
      <span class="social-item"><span class="social-dot"></span>Friendsbook</span>
      <span class="social-item"><span class="social-dot"></span>Snapgram</span>
    </div>
    <p class="centered-line review-prompt">Enjoyed it? Please leave us a review on Craftlane</p>
  </section>

  <section class="brand-card">
    <div class="note-area">
      <p class="note-label">A note for you</p>
      <div class="note-rule"></div>
      <div class="note-rule"></div>
      <div class="note-rule"></div>
    </div>
    <div class="centered-line brand-name">KELVOMILL</div>
  </section>
</main>
</body>
</html>
```